Innovative cost reduction consultant needs to build a group of technical advisors

We need to share our message and compassion for developing cost reduction in the automotive industry. We create opportunities for immediate innovation, by developing cost reduction solutions across suppliers with related process. Attached is an existing Power Point, but it needs improvement. Most of all, a good compelling story, why experts should join us.

Target Market(s)

Automotive industry, supply chain management

Industry/Entity Type

Automotive

Font styles to use
Serif
Sans Serif

Requirements
Must have
• Better visual graphics. There are a few, but they are not as visually appearing as I would like. A graphic with data should have a better visual impact then the ones that I created. I would like to share the message, that I am providing a solution for the automotive industry. The goal is to reduce costs and improve supplier and OEM relationships. The objective is to do so by creating opportunities for immediate innovation, by developing cost reduction solutions across suppliers with related processes. This message may need a visual graphic, which is missing from the presentation.
Nice to have
• Challenge my story and presentation. Does this make sense to you, and what is your opinions of the subject. Or, a relevant news source to validate the story.
Should not have
• I have not decided on the name of the venture or logo. So, let's just use my name as the source or writer. Marcus Delby, Cost Reduction Specialist. Thanks,

```html
<!DOCTYPE html>
<html lang="en">
<head>
<meta charset="UTF-8">
<title>Technical Advisor Group, Value Items</title>
<link rel="stylesheet" href="https://fonts.googleapis.com/css2?family=Roboto+Condensed:wght@300;400;700&display=swap">
<style>
  :root {
    --brand-navy: #0b4c9f;
    --brand-sky: #1f9be2;
    --text-gray: #5a5d63;
    --bullet-blue: #1f5ba8;
    --paper: #ffffff;
    --photo-warm: #f2a253;
    --photo-glow: #fbe3b8;
    --photo-steel: #7d8595;
    --photo-dark: #4b5160;
  }
  * { margin: 0; padding: 0; box-sizing: border-box; }
  html, body { width: 1200px; height: 650px; overflow: hidden; background: var(--paper); }
  .slide {
    position: relative;
    width: 1200px;
    height: 650px;
    background: var(--paper);
    font-family: "Roboto Condensed", "Arial Narrow", sans-serif;
    overflow: hidden;
  }
  .title-band {
    position: absolute;
    left: 0; top: 0;
    width: 1200px; height: 100px;
    background: var(--brand-navy);
  }
  .slide-title {
    position: absolute;
    left: 79px; top: 48px;
    font-size: 42px;
    font-weight: 700;
    color: var(--paper);
    letter-spacing: -0.3px;
    line-height: 1;
  }
  .rail-photo {
    position: absolute;
    left: 540px; top: 100px;
    width: 660px; height: 524px;
    background:
      radial-gradient(ellipse 45% 38% at 48% 18%, var(--photo-glow) 0%, var(--photo-warm) 35%, rgba(242,162,83,0) 75%),
      linear-gradient(180deg, #c9a07a 0%, var(--photo-steel) 45%, var(--photo-dark) 100%);
  }
  .rail-photo::after {
    content: "";
    position: absolute;
    inset: 0;
    background: linear-gradient(90deg, var(--paper) 0%, rgba(255,255,255,0.85) 14%, rgba(255,255,255,0.3) 28%, rgba(255,255,255,0) 40%);
  }
  .value-list {
    position: absolute;
    left: 82px; top: 124px;
    width: 528px;
    list-style: none;
  }
  .value-item {
    position: relative;
    padding-left: 33px;
    font-size: 21px;
    font-weight: 300;
    line-height: 29px;
    color: var(--text-gray);
    text-align: justify;
  }
  .value-item + .value-item { margin-top: 32px; }
  .value-item .arrow {
    position: absolute;
    left: 0; top: 8px;
    width: 9px; height: 13px;
  }
  .sub-list {
    list-style: none;
    margin-top: 8px;
    padding-left: 10px;
  }
  .sub-item {
    position: relative;
    padding-left: 22px;
    font-size: 17.5px;
    line-height: 25px;
    font-weight: 300;
    text-align: justify;
  }
  .sub-item::before {
    content: "";
    position: absolute;
    left: 2px; top: 11px;
    width: 4px; height: 4px;
    border-radius: 50%;
    background: var(--text-gray);
  }
  .footer-band {
    position: absolute;
    left: 0; bottom: 0;
    width: 1200px; height: 26px;
    background: var(--brand-sky);
  }
</style>
</head>
<body>
<div class="slide">
  <div class="title-band"></div>
  <h1 class="slide-title">Technical Advisor Group, Value Items</h1>

  <div class="rail-photo" role="img" aria-label="Photograph of converging railway tracks lit by warm orange sunlight"></div>

  <ul class="value-list">
    <li class="value-item">
      <svg class="arrow" viewBox="0 0 9 13"><path d="M0 0 L9 6.5 L0 13 Z" fill="var(--bullet-blue)"/></svg>
      Manufacturing Traceability and Supply Chain Management tool:
      <ul class="sub-list">
        <li class="sub-item">Imagine, with the touch of a button, knowing the exact airbags that went on 11.5 million vehicles. We have an exclusive partnership with the Silicon Valley start up that is making this tech.</li>
      </ul>
    </li>
    <li class="value-item">
      <svg class="arrow" viewBox="0 0 9 13"><path d="M0 0 L9 6.5 L0 13 Z" fill="var(--bullet-blue)"/></svg>
      Additive Manufacturing or AM, the use of using 3D printer technology will decrease costs of tooling, jigs and fixtures. AM has improved development of complex geometries in tooling, help reduced scrap, and decrease time to market.
    </li>
    <li class="value-item">
      <svg class="arrow" viewBox="0 0 9 13"><path d="M0 0 L9 6.5 L0 13 Z" fill="var(--bullet-blue)"/></svg>
      Capital expenditure planning and capital budget development.
    </li>
  </ul>

  <div class="footer-band"></div>
</div>
</body>
</html>
```